New Business Card Design Project

Need a design that will create an impact / strong impression towards our clients for our business. We are in the lighting business and we do lighting retrofits for large commercial to industrial clientele.

Target Market(s)

Lighting Industry

Industry/Entity Type

Business

Font styles to use
Other font styles liked:
• we would like to use the font on our logo, not sure what it is though..

Requirements
Must have
• Our logo.
Nice to have
• We are open to suggestions that have to do with lighting.

```html
<!DOCTYPE html>
<html lang="en">
<head>
<meta charset="utf-8">
<title>Lumen Shift Group — Business Card</title>
<link href="https://fonts.googleapis.com/css2?family=Lato:wght@400;700;900&display=swap" rel="stylesheet">
<style>
  :root {
    --backdrop: #4a4a4c;
    --forest: #123d12;
    --deep: #0f3a0f;
    --grass: #0a7f35;
    --leaf: #5fc35a;
    --paper: #ffffff;
    --ink-light: #f2f7f2;
  }
  * { margin: 0; padding: 0; box-sizing: border-box; }
  html, body { width: 1200px; height: 900px; overflow: hidden; }
  body {
    background: var(--backdrop);
    font-family: "Lato", Arial, sans-serif;
    position: relative;
  }
  .card {
    position: absolute;
    width: 640px;
    height: 366px;
    overflow: hidden;
    box-shadow: 0 10px 28px rgba(0,0,0,0.45);
  }

  /* Back of card */
  .card-back {
    left: 440px; top: 50px;
    background: var(--forest);
  }
  .card-back .brand {
    position: absolute; left: 0; right: 0; top: 120px;
    display: flex; align-items: center; justify-content: center; gap: 16px;
  }
  .brand-square {
    width: 34px; height: 34px;
    background: var(--leaf);
  }
  .card-back .brand-name {
    color: var(--leaf);
    font-weight: 900;
    font-size: 40px;
    letter-spacing: 1px;
    line-height: 1;
  }
  .card-back .site {
    position: absolute; left: 0; right: 0; top: 282px;
    text-align: center;
    color: var(--ink-light);
    font-size: 17px;
    letter-spacing: 1.5px;
  }

  /* Front of card */
  .card-front {
    left: 120px; top: 470px;
    background: var(--paper);
  }
  .card-front .wave { position: absolute; left: 0; top: 0; }
  .card-front .brand {
    position: absolute; left: 34px; top: 44px;
    display: flex; align-items: center; gap: 14px;
  }
  .card-front .brand-square { background: var(--grass); width: 30px; height: 30px; }
  .card-front .brand-name {
    color: var(--deep);
    font-weight: 900;
    font-size: 36px;
    letter-spacing: 0.5px;
    line-height: 1;
  }
  .address {
    position: absolute; left: 34px; top: 262px;
    color: var(--paper);
    font-size: 17px;
    line-height: 1.3;
  }
  .person {
    position: absolute; left: 400px; top: 208px;
    color: var(--paper);
  }
  .person .name { font-size: 25px; font-weight: 700; line-height: 1.1; }
  .person .role { font-size: 16px; line-height: 1.2; margin-bottom: 8px; }
  .contact { list-style: none; }
  .contact li {
    display: flex; align-items: center; gap: 12px;
    font-size: 16px; line-height: 1.4;
  }
  .contact svg { width: 15px; height: 15px; flex: none; fill: var(--paper); }
</style>
</head>
<body>

<section class="card card-back" aria-label="Card back">
  <div class="brand">
    <span class="brand-square"></span>
    <span class="brand-name">LUMEN SHIFT GROUP, LLC</span>
  </div>
  <p class="site">www.lumenshift-llc.com</p>
</section>

<section class="card card-front" aria-label="Card front">
  <svg class="wave" width="640" height="366" viewBox="0 0 640 366" aria-hidden="true">
    <path d="M0 185 C120 225 240 230 360 200 C460 175 560 158 640 155 L640 366 L0 366 Z" fill="var(--grass)"/>
    <g fill="none">
      <path d="M0 185 C120 225 240 230 360 200 C460 175 560 158 640 155" transform="translate(0,-4)" stroke="var(--paper)" stroke-width="5"/>
      <path d="M0 185 C120 225 240 230 360 200 C460 175 560 158 640 155" transform="translate(0,-12)" stroke="var(--deep)" stroke-width="10"/>
      <path d="M0 185 C120 225 240 230 360 200 C460 175 560 158 640 155" transform="translate(0,-20)" stroke="var(--paper)" stroke-width="5"/>
      <path d="M0 185 C120 225 240 230 360 200 C460 175 560 158 640 155" transform="translate(0,-27)" stroke="var(--grass)" stroke-width="8"/>
    </g>
  </svg>

  <div class="brand">
    <span class="brand-square"></span>
    <span class="brand-name">LUMEN SHIFT<br>GROUP, LLC</span>
  </div>

  <p class="address">2847 North Cedar Avenue<br>Elmhurst, IL 60126</p>

  <div class="person">
    <p class="name">Mark Ellison</p>
    <p class="role">Manager</p>
    <ul class="contact">
      <li><svg viewBox="0 0 16 16" aria-hidden="true"><path d="M3 1l3 3-1.5 2c1 2 2.5 3.5 4.5 4.5L11 9l3 3-2 2.5C6 14 2 10 1 3.5z"/></svg>(555) 214-3300</li>
      <li><svg viewBox="0 0 16 16" aria-hidden="true"><path d="M4 1h8v4H4zM1 6h14v6h-3v3H4v-3H1zM5 10v3h6v-3z"/></svg>(555) 214-3301</li>
      <li><svg viewBox="0 0 16 16" aria-hidden="true"><path d="M1 3h14v10H1zM2 4l6 5 6-5v1L8 10 2 5z" fill-rule="evenodd"/></svg>info@lumenshift-llc.com</li>
      <li><svg viewBox="0 0 16 16" aria-hidden="true"><path d="M8 1a7 7 0 110 14A7 7 0 018 1zm-5.8 6.3h2.6c.1-1.8.5-3.3 1.1-4.4A6 6 0 002.2 7.3zm0 1.4a6 6 0 003.7 4.4c-.6-1.1-1-2.6-1.1-4.4zm4 0c.1 2.3.9 4.3 1.8 4.8.9-.5 1.7-2.5 1.8-4.8zm0-1.4h3.6c-.1-2.3-.9-4.3-1.8-4.8-.9.5-1.7 2.5-1.8 4.8zm5 1.4c-.1 1.800-.5 3.3-1.1 4.4a6 6 0 003.7-4.4zm2.6-1.4a6 6 0 00-3.7-4.4c.6 1.1 1 2.6 1.1 4.4z"/></svg>www.lumenshift-llc.com</li>
    </ul>
  </div>
</section>

</body>
</html>
```